High impact classy folder for an HVAC and Electrical contractor

We need a folder designed. It needs to be high impact and classy with a rich look to it. We want to cement our branding via the use of the folder so the look will need to have impact with use of our logo and colors.

We want to pull the entire brand look and feel together with this folder. We are going to be making other marketing materials and this is the start of a much larger project. In the ideal situation the winning desginer will continue on with the rest of the projects because they will know how to apply the brand look.

We want to give our local company the feel of a national franchise. Wherein the brand is very prominent and is repeated over and over again.

Use of logo and color scheme will be important.

We like dark backgrounds because they really make the logo pop.

Target Market(s)

homeowners

Font styles to use
Serif

Requirements
Must have
• Logo prominent on the front
• Our Tag Line:
• The Best Way To Live In New Jersey Is With Harbel"
• On the inside pockets:
• Our Phone number: 973-555-0148
• A message to our customers:
• We want to thank you for choosing Harbel Tradeworks today
• Our name says it all, because for over 30 years we have prided ourselves on delivering the best service and exceeding our customers' expectations everyday. Whether you need something fixed, replaced or upgraded, no matter how large or small, the dedicated and experts at Harbel Tradeworks are here to take care of you. Delivering the right solution for you the first time- everytime - and ensuring you are always 100% satisfied. If for any reason you want to speak with us, please do not hesitate to call or email. Thank you again for choosing Harbel Tradeworks.
• On the rear: a graphic that says 24-7 service
• A list of other services we provide:
• Solar
• Generators
• Home Security
• Home Automation
• Home Inspection
• Energy Audits
• 1 Day Bathroom remodles
• Basement Waterproofing
• Garage Doors
• Home Theaters
Nice to have
• I added photos of a flyer and of a mobile website to give an idea of the color scheme as well

```html
<!DOCTYPE html>
<html lang="en">
<head>
<meta charset="utf-8">
<title>Harbel Tradeworks – Presentation Folder</title>
<link href="https://fonts.googleapis.com/css2?family=Cinzel:wght@400;700&family=Roboto+Condensed:wght@400;700&display=swap" rel="stylesheet">
<style>
  :root {
    --backdrop: #dcc2a6;
    --orange: #e8803a;
    --red: #a6262a;
    --deep-red: #8e1c22;
    --gold: #e9c27a;
    --cream: #f4e6c8;
    --paper: #f3f3f3;
    --paper-shade: #dcdcdc;
    --ink-grey: #9a9a9a;
    --card: #2c2c2c;
    --call-orange: #f39a4a;
  }
  * { box-sizing: border-box; margin: 0; padding: 0; }
  html, body { width: 1200px; height: 847px; overflow: hidden; }
  body {
    background: var(--backdrop);
    position: relative;
    font-family: "Roboto Condensed", sans-serif;
  }

  /* Front cover */
  .cover {
    position: absolute; left: 70px; top: 190px;
    width: 330px; height: 440px;
    background: linear-gradient(160deg, var(--orange) 0%, #c5452c 45%, var(--red) 100%);
    overflow: hidden;
  }
  .cover__brand {
    position: absolute; top: 78px; left: 0; width: 100%;
    text-align: center;
    font-family: "Cinzel", serif; font-weight: 700;
    color: var(--gold); font-size: 34px; line-height: 1.05;
  }
  .cover__tagline {
    position: absolute; top: 212px; left: 0; width: 100%;
    text-align: center;
    font-family: "Cinzel", serif; font-size: 9.5px;
    color: var(--cream); letter-spacing: .2px;
  }
  .cover__wave { position: absolute; left: 0; top: 238px; width: 330px; height: 40px; }
  .cover__photo {
    position: absolute; left: 0; top: 268px; width: 330px; height: 164px;
    background: linear-gradient(120deg, #8a8580 0%, #d9d6d0 45%, #3a3530 100%);
  }
  .cover__url {
    position: absolute; right: 16px; bottom: 16px;
    font-size: 9px; color: #e8e000;
  }
  .cover__footer { position: absolute; left: 0; bottom: 0; width: 100%; height: 8px; background: var(--deep-red); }

  /* Inside spread */
  .spread { position: absolute; left: 470px; top: 190px; width: 680px; height: 440px; display: flex; }
  .panel { position: relative; width: 340px; height: 440px; background: var(--paper); }
  .panel--right { background: linear-gradient(90deg, var(--paper-shade), var(--paper)); }
  .panel__mark {
    position: absolute; top: 95px; left: 0; width: 100%;
    text-align: center;
    font-family: "Cinzel", serif; font-weight: 700;
    color: var(--ink-grey); font-size: 30px; line-height: 1.05;
  }
  .pocket {
    position: absolute; left: 0; bottom: 0; width: 100%; height: 155px;
    background: linear-gradient(165deg, var(--orange) 0%, #c84a2c 50%, var(--red) 100%);
  }
  .pocket__message { position: absolute; left: 58px; right: 10px; top: 14px; color: #fff; }
  .pocket__heading { font-size: 8px; font-weight: 700; margin-bottom: 4px; }
  .pocket__body { font-size: 5.6px; line-height: 1.55; text-align: justify; }
  .pocket__call {
    position: absolute; left: 58px; bottom: 14px;
    font-size: 24px; font-weight: 700; color: #fff;
  }
  .pocket__call span { color: var(--call-orange); }

  .business-card {
    position: absolute; left: 72px; top: 28px; width: 120px; height: 72px;
    background: var(--card); border-radius: 3px;
    box-shadow: 2px 3px 5px rgba(0,0,0,.35);
  }
  .business-card::before, .business-card::after {
    content: ""; position: absolute; left: 0; width: 100%; height: 3px; background: var(--orange);
  }
  .business-card::before { top: 6px; }
  .business-card::after { bottom: 6px; }
  .business-card__name {
    position: absolute; top: 28px; width: 100%; text-align: center;
    font-size: 10px; font-weight: 700; color: #fff;
  }
</style>
</head>
<body>

  <section class="cover" aria-label="Folder front cover">
    <div class="cover__brand">Harbel<br>Tradeworks</div>
    <p class="cover__tagline">The Best Way To Live In New Jersey Is With Harbel</p>
    <svg class="cover__wave" viewBox="0 0 330 40" preserveAspectRatio="none">
      <path d="M0 40 C80 0 200 10 330 0 L330 40 Z" fill="var(--deep-red)"/>
      <path d="M0 40 C80 8 200 18 330 8" fill="none" stroke="var(--orange)" stroke-width="2"/>
    </svg>
    <div class="cover__photo" role="img" aria-label="Photo of a modern remodelled bathroom with glass shower, round mirrors and dark vanity"></div>
    <span class="cover__url">www.harbeltrade-nj.com</span>
    <div class="cover__footer"></div>
  </section>

  <section class="spread" aria-label="Folder inside spread">
    <div class="panel panel--left">
      <div class="panel__mark">Harbel<br>Tradeworks</div>
      <div class="pocket">
        <div class="pocket__message">
          <p class="pocket__heading">We want to thank you for choosing Harbel Tradeworks today</p>
          <p class="pocket__body">Our name says it all, because for over 30 years we have prided ourselves on delivering the best service and exceeding our customers' expectations everyday. Whether you need something fixed, replaced or upgraded, no matter how large or small, the dedicated and experts at Harbel Tradeworks are here to take care of you. Delivering the right solution for you the first time- everytime - and ensuring you are always 100% satisfied. If for any reason you want to speak with us, please do not hesitate to call or email. Thank you again for choosing Harbel Tradeworks.</p>
        </div>
        <p class="pocket__call">Call Us <span>973-555-0148</span></p>
      </div>
    </div>
    <div class="panel panel--right">
      <div class="panel__mark">Harbel<br>Tradeworks</div>
      <div class="pocket">
        <div class="business-card"><span class="business-card__name">Quillmark Folders</span></div>
      </div>
    </div>
  </section>

</body>
</html>
```